QuillVane needs a dashboard page designed

Redesign the dashboard shown in the provided images.

There are two images:
- dashboard.png
- dashboard-expanded.png

NOTE: The vocabulary navigation on the left will be a very long list of words 100s, so keep that in mind when you're designing both the vocab navigation and the expanded vocab popup.

In the dashboard.png picture, there needs to be a progress chart showing the word progress like the following: review 1(show it as completed) -> review 2(show the user they are here) -> review 3(unvisited) -> review 4(unvisited)

The do-not-design-this-page.png image is for your reference only. It is not to be designed. Use it to understand the overall look and feel of the website to help you create the best dashboard page possible.
Updates

Need extra days to review

Industry/Entity Type

Education English learning

Number of Pages Required

1 page

Requirements
Must have
• The main navigation and main header cannot change between pages. See the do-not-design page for the main navigateion and header.
Should not have
• Do not add a person profile. We will not have images of our users. Keep the icons in the main navigation as they are.

```html
<!DOCTYPE html>
<html lang="en">
<head>
<meta charset="utf-8">
<title>LexiPath Tutor – Vocabulary Dashboard</title>
<link rel="stylesheet" href="https://fonts.googleapis.com/css2?family=Poppins:wght@400;500;600;700&display=swap">
<style>
:root{
  --header:#232a31;
  --rail:#232a31;
  --sidebar:#2d353c;
  --page:#f1f1f1;
  --card:#ffffff;
  --ink:#1f252b;
  --text:#333a40;
  --muted:#9aa2a9;
  --green:#6a9a32;
  --star:#f0a92b;
  --line:#3b444c;
  --band-long:#e9eef2;
  --band-work:#ebf3ea;
  --band-short:#fbeff2;
  --band-forgot:#dcedf4;
}
*{box-sizing:border-box;margin:0;padding:0}
html,body{width:1200px;height:965px;overflow:hidden}
body{font-family:"Poppins",sans-serif;background:var(--page);color:var(--text);position:relative}
.header{position:absolute;left:0;top:0;width:1200px;height:51px;background:var(--header)}
.brand{position:absolute;left:22px;top:10px;color:#fff;font-weight:600;font-size:20px}
.brand small{font-size:11px;margin-left:3px}
.header-icon{position:absolute;top:14px}
.avatar{position:absolute;left:1110px;top:5px;width:40px;height:40px;border-radius:50%;background:linear-gradient(135deg,#c9b6a4,#7b8794)}
.rail{position:absolute;left:0;top:51px;width:77px;height:914px;background:var(--rail)}
.rail-item{position:absolute;left:0;width:77px;text-align:center;color:#fff;font-size:9.5px;line-height:12px}
.rail-divider{position:absolute;left:12px;width:56px;height:1px;background:#3d464e}
.home{width:36px;height:36px;border-radius:50%;background:#fff;margin:0 auto 6px;display:flex;align-items:center;justify-content:center}
.sidebar{position:absolute;left:77px;top:51px;width:220px;height:914px;background:var(--sidebar)}
.select{position:absolute;left:39px;top:35px;width:113px;height:30px;border:1px solid #5a636b;border-radius:2px;color:#fff;font-size:9.5px;font-weight:500;padding:7px 13px}
.select svg{position:absolute;right:10px;top:11px}
.popout{position:absolute;left:282px;top:87px;width:28px;height:28px;border-radius:50%;background:#fff;display:flex;align-items:center;justify-content:center;box-shadow:0 1px 4px rgba(0,0,0,.2)}
.group{position:absolute;left:38px;width:162px}
.group h3{color:#fff;font-size:12px;font-weight:600}
.group .help{position:absolute;right:0;top:2px}
.group .active{color:var(--green);font-size:9.5px;font-weight:700;margin-top:7px}
.group ul{list-style:none;margin-top:6px}
.group li{color:var(--muted);font-size:10px;line-height:15px;padding-left:13px;position:relative}
.group li::before{content:"";position:absolute;left:1px;top:5px;width:4px;height:4px;border-right:1px solid #cfd4d8;border-top:1px solid #cfd4d8;transform:rotate(45deg)}
.side-divider{position:absolute;left:39px;width:161px;height:1px;background:#48515a}
.steps{position:absolute;left:320px;top:78px;width:540px;height:100px}
.step{position:absolute;width:110px;text-align:center;margin-left:-55px}
.step .label{font-size:9.5px;font-weight:500;color:var(--ink)}
.step .dot{width:54px;height:54px;border-radius:50%;margin:8px auto 8px;display:flex;align-items:center;justify-content:center}
.step .state{font-size:12px;color:var(--ink)}
.connector{position:absolute;top:46px;height:3px}
.word-title{position:absolute;left:343px;top:225px;font-size:20px;font-weight:600;color:var(--ink);display:flex;align-items:center;gap:8px}
.cta{position:absolute;left:924px;top:205px;width:239px;height:39px;border-radius:20px;background:var(--header);color:#fff;font-size:8.5px;font-weight:700;display:flex;align-items:center;justify-content:center;gap:8px}
.card{position:absolute;left:337px;width:825px;background:var(--card);border-radius:15px;box-shadow:0 1px 3px rgba(0,0,0,.05)}
.card p{font-size:11.5px;line-height:17.3px;color:var(--ink)}
.card b{font-weight:600}
.section-title{position:absolute;left:335px;font-size:19.5px;font-weight:600;color:var(--ink)}
</style>
</head>
<body>
<header class="header">
  <div class="brand">LexiPath Tutor<small>⌄</small></div>
  <svg class="header-icon" style="left:1041px" width="20" height="20" viewBox="0 0 24 24" fill="none" stroke="#fff" stroke-width="1.6"><circle cx="12" cy="12" r="3.2"/><path d="M12 2.5l1.6 2.4 2.8-.8.6 2.8 2.8.6-.8 2.8 2.4 1.7-2.4 1.6.8 2.8-2.8.6-.6 2.8-2.8-.8L12 21.5l-1.6-2.4-2.8.8-.6-2.8-2.8-.6.8-2.8L2.5 12l2.5-1.7-.8-2.8 2.8-.6.6-2.8 2.8.8z"/></svg>
  <svg class="header-icon" style="left:1071px" width="20" height="20" viewBox="0 0 24 24" fill="none" stroke="#fff" stroke-width="1.6"><path d="M6 17V11a6 6 0 0 1 12 0v6l2 2H4z"/><path d="M10 21h4"/><circle cx="17" cy="6" r="2.5"/></svg>
  <div class="avatar" role="img" aria-label="User profile photo"></div>
  <svg class="header-icon" style="left:1159px;top:21px" width="10" height="8" viewBox="0 0 10 8" fill="none" stroke="#fff" stroke-width="1.6"><path d="M1 2l4 4 4-4"/></svg>
</header>

<nav class="rail">
  <div class="rail-item" style="top:31px">
    <div class="home"><svg width="16" height="16" viewBox="0 0 24 24" fill="var(--header)"><path d="M12 3l9 8h-3v9h-4v-6h-4v6H6v-9H3z"/></svg></div>
    LexiPath<br>Tutor
  </div>
  <div class="rail-divider" style="top:124px"></div>
  <div class="rail-item" style="top:145px">
    <svg width="14" height="16" viewBox="0 0 24 28" fill="#fff"><path d="M12 1a9 9 0 0 0-9 9c0 7 9 17 9 17s9-10 9-17a9 9 0 0 0-9-9zm0 12.5A3.5 3.5 0 1 1 12 6.5a3.5 3.5 0 0 1 0 7z"/></svg><br>
    <span style="display:block;margin-top:2px">Daily<br>English</span>
  </div>
  <div class="rail-divider" style="top:213px"></div>
  <div class="rail-item" style="top:235px">
    <svg width="16" height="20" viewBox="0 0 16 20" fill="#fff"><path d="M1 1h14v19H10v-4H6v4H1zM4 4v2h2V4zm6 0v2h2V4zM4 8v2h2V8zm6 0v2h2V8zM4 12v2h2v-2zm6 0v2h2v-2z"/></svg><br>
    <span style="display:block;margin-top:4px">Business</span>
  </div>
</nav>

<aside class="sidebar">
  <div class="select">ALL<svg width="8" height="6" viewBox="0 0 8 6" fill="none" stroke="#fff" stroke-width="1.4"><path d="M1 1l3 3 3-3"/></svg></div>
  <div class="group" style="top:94px">
    <h3>Short-Term Memory</h3>
    <svg class="help" width="13" height="13" viewBox="0 0 14 14" fill="none" stroke="#fff"><circle cx="7" cy="7" r="6"/><text x="7" y="10" font-size="8" text-anchor="middle" fill="#fff" stroke="none" font-family="Poppins,sans-serif">?</text></svg>
    <div class="active">GRAB</div>
  </div>
  <div class="side-divider" style="top:151px"></div>
  <div class="group" style="top:171px">
    <h3>Working Memory</h3>
    <svg class="help" width="13" height="13" viewBox="0 0 14 14" fill="none" stroke="#fff"><circle cx="7" cy="7" r="6"/><text x="7" y="10" font-size="8" text-anchor="middle" fill="#fff" stroke="none" font-family="Poppins,sans-serif">?</text></svg>
    <ul>
      <li>Cool Down</li><li>Crav</li><li>Go For</li><li>Go-To</li><li>In The Mood For</li><li>Sip</li><li>Soothing</li><li>Stick With</li><li>Throw In/Throw On</li>
    </ul>
  </div>
  <div class="side-divider" style="top:349px"></div>
  <div class="group" style="top:367px">
    <h3>Long-Term Memory</h3>
    <svg class="help" width="13" height="13" viewBox="0 0 14 14" fill="none" stroke="#fff"><circle cx="7" cy="7" r="6"/><text x="7" y="10" font-size="8" text-anchor="middle" fill="#fff" stroke="none" font-family="Poppins,sans-serif">?</text></svg>
    <ul><li>Give ItA Try</li></ul>
  </div>
</aside>
<div class="popout"><svg width="12" height="12" viewBox="0 0 12 12" fill="none" stroke="#333" stroke-width="1.2"><path d="M5 2H2v8h8V7M7 1h4v4M11 1L5.5 6.5"/></svg></div>

<section class="steps">
  <div class="connector" style="left:49px;width:289px;background:var(--line)"></div>
  <div class="connector" style="left:338px;width:143px;background:#dcdcdc"></div>
  <div class="step" style="left:49px">
    <div class="label">REVIEW 1</div>
    <div class="dot" style="background:var(--green)"><svg width="26" height="26" viewBox="0 0 26 26"><circle cx="13" cy="13" r="12" fill="#fff"/><path d="M7.5 13.5l3.8 3.5 7-7.5" fill="none" stroke="var(--green)" stroke-width="2.8"/></svg></div>
    <div class="state">Completed</div>
  </div>
  <div class="step" style="left:193px">
    <div class="label">REVIEW 2</div>
    <div class="dot" style="background:var(--header)"><svg width="20" height="22" viewBox="0 0 20 22" fill="#fff"><circle cx="10" cy="6" r="5"/><path d="M0 22c0-6 4-9 10-9s10 3 10 9z"/></svg></div>
    <div class="state">You are here</div>
  </div>
  <div class="step" style="left:338px">
    <div class="label">REVIEW 3</div>
    <div class="dot" style="border:1.5px solid var(--line);background:var(--page)"></div>
    <div class="state">Unvisited</div>
  </div>
  <div class="step" style="left:481px">
    <div class="label">REVIEW 4</div>
    <div class="dot" style="border:1.5px solid var(--line);background:var(--page)"></div>
    <div class="state">Unvisited</div>
  </div>
</section>

<h1 class="word-title">Grab <svg width="18" height="18" viewBox="0 0 24 24" fill="var(--star)"><path d="M12 2l3 6.6 7.2.7-5.4 4.9 1.6 7.1L12 17.6 5.6 21.3l1.6-7.1L1.8 9.3 9 8.6z"/></svg></h1>
<div class="cta"><svg width="7" height="8" viewBox="0 0 7 8" fill="#fff"><path d="M0 0l7 4-7 4z"/></svg>START VOCABULARY REVIEW EXERCISE 3</div>

<div class="card" style="top:269px;height:112px;padding:20px 32px">
  <p>The word <b>"grab"</b> is most commonly used as a <b>verb,</b> meaning <b>to take something quickly or suddenly</b>. Imagine you're running late for school. You don't have time for breakfast, so you quickly <b>grab</b> an apple from the kitchen and rush out the door. As you reach the bus stop, your friend waves &amp; says, "Hey! Let's <b>grab</b> a coffee after class." Later, when you sit down, your phone starts ringing. You <b>grab</b> it from your bag and answer.</p>
</div>

<h2 class="section-title" style="top:414px">Learning Curve Graph</h2>
<div class="card" style="top:455px;height:301px">
  <svg width="825" height="301" viewBox="0 0 825 301" font-family="Poppins,sans-serif">
    <defs>
      <linearGradient id="fade" x1="0" x2="1"><stop offset="0" stop-color="#fff" stop-opacity="0"/><stop offset="1" stop-color="#fff" stop-opacity=".9"/></linearGradient>
    </defs>
    <rect x="27" y="23" width="772" height="45" fill="var(--band-long)"/>
    <rect x="27" y="69" width="772" height="102" fill="var(--band-work)"/>
    <rect x="27" y="171" width="772" height="33" fill="var(--band-short)"/>
    <rect x="27" y="204" width="772" height="32" fill="var(--band-forgot)"/>
    <rect x="27" y="23" width="772" height="213" fill="url(#fade)"/>
    <g font-size="8.5" fill="#555c62">
      <text x="39" y="49">Long-term Memory</text>
      <text x="39" y="124">Working Memory</text>
      <text x="39" y="191">Short-Term Memory</text>
      <text x="39" y="223">Forgotten Memory</text>
    </g>
    <line x1="27" y1="236" x2="799" y2="236" stroke="#cfd3d6"/>
    <g stroke="#b9bec2">
      <path d="M41 236v7M85 236v7M129 236v7M173 236v7M217 236v7M261 236v7M305 236v7M349 236v7M393 236v7M437 236v7M481 236v7M525 236v7M569 236v7M613 236v7M657 236v7M701 236v7M745 236v7M789 236v7"/>
    </g>
    <g font-size="7.5" fill="#333" text-anchor="middle">
      <text x="41" y="261">18 May</text><text x="85" y="261">12:00</text><text x="129" y="261">19 May</text><text x="173" y="261">12:00</text>
      <text x="217" y="261">20 May</text><text x="261" y="261">12:00</text><text x="305" y="261">21 May</text><text x="349" y="261">12:00</text>
      <text x="393" y="261">22 May</text><text x="437" y="261">12:00</text><text x="481" y="261">23 May</text><text x="525" y="261">12:00</text>
      <text x="569" y="261">24 May</text><text x="613" y="261">12:00</text><text x="657" y="261">25 May</text><text x="701" y="261">12:00</text>
      <text x="745" y="261">26 May</text><text x="789" y="261">12:00</text>
    </g>
    <text x="412" y="287" font-size="8.5" font-weight="600" fill="#222" text-anchor="middle">DATE RANGE</text>
    <path d="M309 187C350 187 375 205 390 236" fill="none" stroke="#777" stroke-width="1" stroke-dasharray="1.5 2.5"/>
    <path d="M399 91C500 91 565 140 570 236" fill="none" stroke="#777" stroke-width="1" stroke-dasharray="1.5 2.5"/>
    <rect x="303" y="186" width="7" height="51" rx="3" fill="var(--header)"/>
    <rect x="393" y="89" width="7" height="148" rx="3" fill="var(--header)"/>
    <g font-size="7.5" fill="#222" text-anchor="middle">
      <rect x="287" y="163" width="40" height="17" rx="3" fill="#fff" stroke="#e2e2e2"/><text x="307" y="175">21 May</text>
      <rect x="375" y="61" width="42" height="17" rx="3" fill="#fff" stroke="#e2e2e2"/><text x="396" y="73">22 May</text>
    </g>
  </svg>
</div>

<h2 class="section-title" style="top:788px">LexiPath Tutor Learning Analysis</h2>
<div class="card" style="top:829px;height:97px;padding:21px 27px">
  <p>Lorem ipsum <b>dolor</b> sit amet, consectetur adipiscing elit. Nam <b>rutrum commodo</b> enim id bibendum. Nunc dignissim risus <b>dolor</b>nec finibus dictum eu. Aliquam sit amet euismod metus, quis malesuada erat. Sed at felis quis nulla feugiat cursus at at <b>dolor</b>. Maecenas pretium aliquet dapibus. Fusce et eleifend massa.&nbsp; Sed convallis ex mi, at lobortis ligula congue vel.</p>
</div>
</body>
</html>
```